KLV Plant Services

We are a heavy diesel mechanical business with additional air con certificates, remapping engine rebuilt

Contact Information for Business Card

Company Name, Director Name, Managing Director, Contact details, email and website

Font styles to use
Serif
Script

```html
<!DOCTYPE html>
<html lang="en">
<head>
<meta charset="utf-8">
<title>KLV Plant Services – Business Card</title>
<link rel="stylesheet" href="https://fonts.googleapis.com/css2?family=Playfair+Display:wght@700&family=Lora:wght@400;500&family=Great+Vibes&display=swap">
<style>
  :root {
    --backdrop: #cfcfcf;
    --card: #ffffff;
    --navy: #141673;
    --ink: #1a1a1a;
    --rule: #2a2a2a;
  }
  * { box-sizing: border-box; margin: 0; padding: 0; }
  html, body {
    width: 1146px; height: 1200px; overflow: hidden;
    background: var(--backdrop);
    font-family: "Lora", serif;
  }
  .card {
    position: absolute;
    left: 235px;
    width: 686px;
    height: 393px;
    background: var(--card);
  }
  .card--front { top: 146px; }
  .card--back { top: 621px; }

  .brand {
    position: absolute;
    display: flex;
    align-items: center;
    gap: 12px;
    color: var(--navy);
    font-family: "Playfair Display", serif;
    font-weight: 700;
    line-height: 1.08;
  }
  .brand__dot {
    flex: none;
    border-radius: 50%;
    background: var(--navy);
  }
  .card--front .brand { left: 440px; top: 74px; width: 220px; font-size: 34px; }
  .card--front .brand__dot { width: 22px; height: 22px; }
  .card--back .brand {
    left: 0; right: 0; top: 162px;
    justify-content: center; font-size: 48px;
  }
  .card--back .brand__dot { width: 30px; height: 30px; }

  .person { position: absolute; left: 36px; top: 204px; }
  .person__name {
    color: var(--navy);
    font-family: "Playfair Display", serif;
    font-size: 31px;
    font-weight: 700;
    letter-spacing: 1.5px;
    line-height: 40px;
  }
  .person__role {
    margin-top: 0;
    color: var(--ink);
    font-family: "Great Vibes", cursive;
    font-size: 27px;
    line-height: 30px;
  }
  .divider {
    position: absolute;
    left: 36px; top: 280px;
    width: 630px; height: 1.5px;
    background: var(--rule);
  }
  .contacts {
    position: absolute;
    left: 36px; top: 289px;
    list-style: none;
    color: var(--ink);
    font-size: 18px;
  }
  .contacts li {
    display: flex; align-items: center; gap: 10px;
    height: 27.5px;
  }
  .contacts svg { width: 18px; height: 18px; fill: var(--navy); flex: none; }
  .address {
    position: absolute;
    right: 36px; top: 310px;
    text-align: right;
    color: var(--ink);
    font-size: 18px;
    line-height: 27px;
    font-style: normal;
  }
</style>
</head>
<body>
  <section class="card card--front">
    <div class="brand"><span class="brand__dot"></span><span>KLV Plant Services</span></div>

    <div class="person">
      <h1 class="person__name">DANIEL HARPER</h1>
      <p class="person__role">Managing Director</p>
    </div>

    <div class="divider"></div>

    <ul class="contacts">
      <li>
        <svg viewBox="0 0 24 24" aria-hidden="true"><path d="M6.6 10.8a15.1 15.1 0 0 0 6.6 6.6l2.2-2.2a1 1 0 0 1 1-.25 11.4 11.4 0 0 0 3.6.57 1 1 0 0 1 1 1V20a1 1 0 0 1-1 1A17 17 0 0 1 3 4a1 1 0 0 1 1-1h3.5a1 1 0 0 1 1 1c0 1.25.2 2.46.57 3.58a1 1 0 0 1-.25 1z"/></svg>
        044-123 456 789
      </li>
      <li>
        <svg viewBox="0 0 24 24" aria-hidden="true"><path d="M2 5h20v14H2z M3.5 6.5 12 13l8.5-6.5" fill="none" stroke="#141673" stroke-width="2"/><path d="M2 5h20L12 12.5z"/></svg>
        info@webname.com
      </li>
      <li>
        <svg viewBox="0 0 24 24" aria-hidden="true"><g fill="none" stroke="#141673" stroke-width="2"><circle cx="12" cy="12" r="9.5"/><ellipse cx="12" cy="12" rx="4" ry="9.5"/><path d="M2.5 12h19M4 7h16M4 17h16"/></g></svg>
        www.websitename.com
      </li>
    </ul>

    <address class="address">
      421, Address line goes here<br>
      45452, Country name
    </address>
  </section>

  <section class="card card--back">
    <div class="brand"><span class="brand__dot"></span><span>KLV Plant Services</span></div>
  </section>
</body>
</html>
```